Fitness website

Website for a fitness brand (see attached specs). Design needs to be modern and vibrant with CTAs on every page. We will provide logos, images, etc but for now user placeholder text and images. For now use the name 'Corvane Athletics' as the name to use on the design. The goal of this site is to either get people to join the gym (5 physical locations across the US); buy an online program; buy merch or supplements or sign up for the newsletter. Pleas use images from this foldeR: https://filebarn.example/share/folders/8QwTz41mKpLrXv93NdYe7HsaBuJ0Cf2_R?usp=sharing

We will be coding this in ReactNative. Lots more work for the winner as well, this is a 1st project for us.

Target Market(s)

fitness enthusiats

Industry/Entity Type

fitness, health, wellness

Number of Pages Required

5+ page

Font styles to use
Other font styles liked:
• Lato

Colors
0054AA
0677BA
7BADD7
CADEEF
E8F1F8
0094D4
00A9DD
6FCCEA
C7EBF8
E9F6FB
00AB8E
00BBA5
67D7C9
C6EFE9
E9F9F6
EE7325
F08F49
F5BC92
FAE3D3
FDF4ED

Requirements
Must have
• must be reactive. most people will view it first on mobile
Nice to have
• video in hero section of top of home page

```html
<!DOCTYPE html>
<html lang="en">
<head>
<meta charset="utf-8">
<title>Corvane Athletics – Home</title>
<link rel="stylesheet" href="https://fonts.googleapis.com/css2?family=Outfit:wght@400;500;600;700&family=Lato:wght@400;700;900&display=swap">
<style>
:root{
  --navy:#050e1d;
  --navy-2:#0a1a33;
  --blue:#163b73;
  --blue-line:#2a5fae;
  --green:#12883b;
  --green-bright:#1fae4a;
  --cream:#fbf9ec;
  --white:#ffffff;
  --ink:#0b1424;
  --muted:#3c4656;
  --star:#f2b01e;
}
*{box-sizing:border-box;margin:0;padding:0}
html,body{width:1200px;height:3814px;overflow:hidden;background:var(--navy)}
body{font-family:'Lato',sans-serif;color:var(--white)}
.page{position:relative;width:1200px;height:3814px;overflow:hidden;background:var(--navy)}
.abs{position:absolute}
h1,h2,h3,.display{font-family:'Outfit',sans-serif}
.ph{position:absolute}
.btn{position:absolute;display:flex;align-items:center;justify-content:space-between;border-radius:30px;font-family:'Outfit',sans-serif;font-weight:600;font-size:11px;letter-spacing:.3px;text-transform:uppercase;color:var(--white);padding:0 6px 0 20px}
.btn-green{background:var(--green)}
.btn-outline{border:1.5px solid #cfd4dc;background:rgba(0,0,0,.25)}
.btn .arrow{width:26px;height:26px;border-radius:50%;background:var(--white);display:flex;align-items:center;justify-content:center}
.btn-outline .arrow{background:var(--white)}

/* header */
.logo-text{font-family:'Outfit',sans-serif;font-weight:600;font-size:19px;letter-spacing:.2px;color:var(--white)}
.nav{position:absolute;left:363px;top:33px;display:flex;gap:18px;font-family:'Outfit',sans-serif;font-size:11px;font-weight:500}
.nav span{display:flex;align-items:center;gap:5px}
.icon-circle{position:absolute;width:22px;height:22px;border:1.5px solid #fff;border-radius:50%;display:flex;align-items:center;justify-content:center}

/* hero */
.hero-title{position:absolute;left:119px;top:188px;font-size:62px;line-height:62px;font-weight:500;color:var(--white)}
.hero-title em{font-style:normal;color:var(--green-bright)}
.hero-sub{position:absolute;left:121px;top:392px;font-size:17px;line-height:22px;color:#e8ecf2}
.play{position:absolute;left:1014px;top:545px;width:60px;height:60px;border-radius:50%;background:rgba(255,255,255,.3);display:flex;align-items:center;justify-content:center}
.play .inner{width:42px;height:42px;border-radius:50%;background:#fff;display:flex;align-items:center;justify-content:center}

/* about */
.about-card{position:absolute;left:690px;top:719px;width:387px;height:362px;background:var(--cream);border-radius:6px;color:var(--ink);padding:22px 27px}
.about-card h2{font-size:33px;line-height:40px;font-weight:600;color:var(--ink)}
.about-card p{font-size:10.8px;line-height:16.6px;color:var(--muted);margin-top:12px}
.feature{position:absolute;top:1117px;display:flex;gap:10px}
.feature .ring{width:66px;height:66px;border-radius:50%;border:2px solid var(--green-bright);display:flex;align-items:center;justify-content:center}
.feature .ring div{width:52px;height:52px;border-radius:50%;background:var(--green);display:flex;align-items:center;justify-content:center}
.feature h3{font-size:16px;font-weight:600;margin-top:10px;line-height:19px}
.feature p{font-size:10.5px;line-height:14px;color:#d4dae4;margin-top:3px}

/* programs */
.programs{position:absolute;left:0;top:1249px;width:1200px;height:529px;background:radial-gradient(ellipse at 50% 40%,#1f4c8d,#163b73 55%,#10305f)}
.section-title{position:absolute;width:1200px;text-align:center;font-size:33px;font-weight:500;color:#fff}
.program-card{position:absolute;top:111px;width:225px;height:278px;border-radius:3px;overflow:hidden}
.program-card .label{position:absolute;left:8px;right:8px;bottom:0;height:37px;background:var(--cream);color:var(--ink);font-family:'Outfit',sans-serif;font-size:16px;font-weight:500;display:flex;align-items:center;justify-content:center;border-radius:3px 3px 0 0}
.nav-arrow{position:absolute;width:26px;height:26px;border-radius:50%;background:#fff;display:flex;align-items:center;justify-content:center}

/* testimonials */
.testi{position:absolute;top:1890px;width:469px;height:231px;background:var(--cream);border-radius:3px;color:var(--ink)}
.testi .photo{position:absolute;left:14px;top:14px;width:213px;height:204px;border:3px solid var(--green);border-radius:4px}
.testi .avatar{position:absolute;left:245px;top:46px;width:48px;height:48px;border-radius:50%;background:linear-gradient(135deg,#3b4a63,#8593a8);border:2px solid #fff}
.testi .name{position:absolute;left:308px;top:53px;font-family:'Outfit',sans-serif;font-size:16px}
.testi .stars{position:absolute;left:308px;top:74px;display:flex;gap:2px}
.testi .quote{position:absolute;left:249px;top:115px;width:210px;font-size:10.8px;line-height:16.6px;color:var(--muted)}
.testi .qmark{position:absolute;right:16px;top:10px}

/* blog */
.blog-img{position:absolute;top:2249px;width:306px;height:320px}
.blog-title{position:absolute;top:2598px;width:250px;font-family:'Outfit',sans-serif;font-size:16px;line-height:21px;font-weight:500}
.blog-go{position:absolute;top:2598px;width:26px;height:26px;border-radius:50%;border:1.5px solid #4d7fd6;display:flex;align-items:center;justify-content:center}
.blog-rule{position:absolute;top:2656px;width:306px;height:1px;background:#2a3446}

/* locations */
.loc-card{position:absolute;left:123px;top:2720px;width:386px;height:311px;background:var(--cream);border-radius:6px;color:var(--ink);overflow:hidden}
.loc-card h2{position:absolute;left:38px;top:20px;font-size:34px;font-weight:500}
.loc-row{position:absolute;left:0;width:386px;height:38px;display:flex;align-items:center;padding-left:38px;gap:14px;font-size:14px;color:var(--ink)}
.loc-row.active{background:var(--green);color:#fff}
.pin{width:28px;height:28px;border-radius:50%;border:1.5px solid currentColor;display:flex;align-items:center;justify-content:center}

/* newsletter */
.bigword{position:absolute;left:30px;top:3140px;width:1170px;font-family:'Outfit',sans-serif;font-weight:700;font-size:118px;letter-spacing:-1px;color:#172132;white-space:nowrap}
.news{position:absolute;left:0;top:3247px;width:1200px;height:297px;background:var(--green)}
.news h2{position:absolute;left:538px;top:72px;font-size:33px;font-weight:500}
.news p{position:absolute;left:538px;top:123px;font-size:13px;color:#e8f5ec}
.news .field{position:absolute;left:544px;top:163px;width:406px;height:42px;border-radius:24px;background:#fff;color:#5a6270;font-size:11px;display:flex;align-items:center;padding-left:20px}
.news .sub{position:absolute;left:266px;top:3px;width:137px;height:36px;background:var(--green);border-radius:20px;display:flex;align-items:center;justify-content:space-between;padding:0 5px 0 28px;color:#fff;font-family:'Outfit',sans-serif;font-weight:600;font-size:11px}

/* footer */
.footer{position:absolute;left:0;top:3544px;width:1200px;height:270px;background:var(--navy)}
.fcol{position:absolute;top:62px}
.fcol h4{font-family:'Outfit',sans-serif;font-weight:500;font-size:15px;margin-bottom:14px}
.fcol li{list-style:none;font-size:9.5px;line-height:20.5px;color:#d3d8e0}
.fdiv{position:absolute;top:50px;width:1px;height:190px;background:#1d283a}
.fcontact{display:flex;align-items:center;gap:12px;font-size:9.5px;margin-bottom:14px}
.fcontact .c{width:22px;height:22px;border-radius:50%;border:1.5px solid #fff;display:flex;align-items:center;justify-content:center}
.social{display:flex;align-items:center;gap:12px;font-size:9.5px;margin-bottom:14px;color:#d3d8e0}
.social .c{width:22px;height:22px;border-radius:50%;border:1.5px solid #fff}
</style>
</head>
<body>
<div class="page">

<!-- HERO -->
<section>
  <div class="ph" role="img" aria-label="Female athlete in a white tank top gripping a barbell inside a dark gym rig" style="left:0;top:0;width:1200px;height:674px;background:linear-gradient(100deg,#0d1522 0%,#1a2330 40%,#3a414b 62%,#252c36 78%,#141b26 100%)"></div>
  <div class="abs" style="left:0;top:0;width:1200px;height:674px;background:linear-gradient(90deg,rgba(5,12,24,.75),rgba(5,12,24,0) 55%)"></div>

  <div class="abs logo-text" style="left:120px;top:28px">CORVANE ATHLETICS</div>
  <nav class="nav">
    <span>ABOUT <svg width="8" height="5" viewBox="0 0 8 5"><path d="M1 1l3 3 3-3" stroke="#fff" fill="none"/></svg></span>
    <span>PROGRAMS <svg width="8" height="5" viewBox="0 0 8 5"><path d="M1 1l3 3 3-3" stroke="#fff" fill="none"/></svg></span>
    <span>AFFILIATES <svg width="8" height="5" viewBox="0 0 8 5"><path d="M1 1l3 3 3-3" stroke="#fff" fill="none"/></svg></span>
    <span>BLOG <svg width="8" height="5" viewBox="0 0 8 5"><path d="M1 1l3 3 3-3" stroke="#fff" fill="none"/></svg></span>
    <span>LOCATION <svg width="8" height="5" viewBox="0 0 8 5"><path d="M1 1l3 3 3-3" stroke="#fff" fill="none"/></svg></span>
    <span>SHOP <svg width="8" height="5" viewBox="0 0 8 5"><path d="M1 1l3 3 3-3" stroke="#fff" fill="none"/></svg></span>
    <span>CONTACT US</span>
  </nav>
  <div class="icon-circle" style="left:906px;top:30px"><svg width="10" height="10" viewBox="0 0 10 10"><circle cx="5" cy="3" r="2.2" fill="#fff"/><path d="M1 10a4 4 0 018 0z" fill="#fff"/></svg></div>
  <div class="icon-circle" style="left:934px;top:30px"><svg width="10" height="10" viewBox="0 0 10 10"><circle cx="4.2" cy="4.2" r="3" stroke="#fff" fill="none" stroke-width="1.3"/><path d="M6.5 6.5l2.5 2.5" stroke="#fff" stroke-width="1.3"/></svg></div>
  <div class="btn btn-green" style="left:966px;top:25px;width:111px;height:33px">JOIN NOW <span class="arrow" style="width:22px;height:22px"><svg width="10" height="10" viewBox="0 0 10 10"><path d="M1 5h8M5.5 1.5L9 5 5.5 8.5" stroke="#12883b" stroke-width="1.5" fill="none"/></svg></span></div>

  <h1 class="hero-title">Unleash Your<br>Potential with<br>Corvane <em>Fitness</em></h1>
  <p class="hero-sub">Train with elite coaches, proven programs, and<br>a community that drives you to be your best.</p>
  <div class="btn btn-green" style="left:121px;top:463px;width:171px;height:39px">EXPLORE PROGRAMS <span class="arrow"><svg width="12" height="12" viewBox="0 0 10 10"><path d="M1 5h8M5.5 1.5L9 5 5.5 8.5" stroke="#12883b" stroke-width="1.4" fill="none"/></svg></span></div>
  <div class="btn btn-outline" style="left:304px;top:463px;width:176px;height:39px">FIND A GYM NEAR YOU <span class="arrow"><svg width="12" height="12" viewBox="0 0 10 10"><path d="M1 5h8M5.5 1.5L9 5 5.5 8.5" stroke="#0b1424" stroke-width="1.4" fill="none"/></svg></span></div>
  <div class="play"><div class="inner"><svg width="16" height="18" viewBox="0 0 16 18"><path d="M2 1l13 8-13 8z" fill="#12883b"/></svg></div></div>
</section>

<!-- ABOUT -->
<section>
  <div class="ph" role="img" aria-label="Athlete jumping rope in a competition arena with judges seated at the sides" style="left:123px;top:720px;width:548px;height:358px;border:4px solid var(--blue-line);border-radius:6px;background:linear-gradient(180deg,#0e1522,#2a313c 60%,#4a4f56)"></div>
  <div class="about-card">
    <h2>About<br>Corvane Athletics</h2>
    <p>At Corvane Athletics, we believe that everyone has the power to be stronger, faster, and more resilient. Our mission is simple: to provide world-class training, expert guidance, and a supportive community that inspires you to push past limits — whether in one of our 5 state-of-the-art gyms across the U.S. or from the comfort of your home with our online programs.</p>
    <p>Founded by passionate athletes and certified trainers, Corvane Athletics started with one goal: to create a place where results, community, and experience come together.</p>
  </div>
  <div class="btn btn-green" style="left:718px;top:1019px;width:171px;height:37px">MEET OUR COACHES <span class="arrow"><svg width="12" height="12" viewBox="0 0 10 10"><path d="M1 5h8M5.5 1.5L9 5 5.5 8.5" stroke="#12883b" stroke-width="1.4" fill="none"/></svg></span></div>

  <div class="feature" style="left:121px">
    <div class="ring"><div><svg width="28" height="26" viewBox="0 0 28 26"><path d="M14 24S2 16 2 8a6 6 0 0112-1 6 6 0 0112 1c0 8-12 16-12 16z" fill="none" stroke="#fff" stroke-width="2"/><circle cx="14" cy="12" r="3" fill="#fff"/></svg></div></div>
    <div><h3>Community First</h3><p>Join a supportive network<br>of motivated members.</p></div>
  </div>
  <div class="feature" style="left:349px">
    <div class="ring"><div><svg width="28" height="24" viewBox="0 0 28 24"><circle cx="14" cy="6" r="4" fill="#fff"/><circle cx="5" cy="9" r="3" fill="#fff"/><circle cx="23" cy="9" r="3" fill="#fff"/><path d="M7 22a7 7 0 0114 0zM0 22a5 5 0 0110-2v2zM28 22a5 5 0 00-10-2v2z" fill="#fff"/></svg></div></div>
    <div><h3>Expert Coaching</h3><p>Certified trainers guide<br>you every step of the way.</p></div>
  </div>
  <div class="feature" style="left:576px">
    <div class="ring"><div><svg width="26" height="26" viewBox="0 0 26 26"><path d="M13 25V12M13 12L5 4M13 12l8-8M3 2h5v0M5 2H2v3M23 2h-3M24 2v3" stroke="#fff" stroke-width="2.2" fill="none"/></svg></div></div>
    <div><h3>Flexible Options</h3><p>In-person, online, or personal<br>coaching — train your way.</p></div>
  </div>
  <div class="feature" style="left:820px">
    <div class="ring"><div><svg width="28" height="24" viewBox="0 0 28 24"><path d="M7 2h14l5 6-12 14L2 8z M2 8h24M10 2l4 20 4-20" stroke="#fff" stroke-width="1.8" fill="none"/></svg></div></div>
    <div><h3>Premium Facilities<br>&amp; Gear</h3><p>Cutting-edge equipment &amp;<br>supplements to power your progress.</p></div>
  </div>
</section>

<!-- PROGRAMS -->
<section class="programs">
  <h2 class="section-title" style="top:46px">Featured Programs</h2>
  <div class="program-card" style="left:126px"><div class="ph" role="img" aria-label="Masters athlete resting hands on knees during a workout" style="inset:0;background:linear-gradient(180deg,#3a3f47,#23272e)"></div><div class="label">Masters</div></div>
  <div class="program-card" style="left:367px"><div class="ph" role="img" aria-label="Athlete in mint top running through a training hall" style="inset:0;background:linear-gradient(180deg,#5c6068,#30353d)"></div><div class="label">Functional Fitness</div></div>
  <div class="program-card" style="left:610px"><div class="ph" role="img" aria-label="Competitor lifting a loaded barbell at an event" style="inset:0;background:linear-gradient(180deg,#464b54,#262a31)"></div><div class="label">Competitive</div></div>
  <div class="program-card" style="left:855px"><div class="ph" role="img" aria-label="Hands holding a bowl of fresh green salad" style="inset:0;background:linear-gradient(180deg,#3b4148,#2e5a2a 60%,#2a2f35)"></div><div class="label">Nutrition</div></div>
  <div class="nav-arrow" style="left:73px;top:245px"><svg width="12" height="12" viewBox="0 0 10 10"><path d="M9 5H1M4.5 1.5L1 5l3.5 3.5" stroke="#0b1424" stroke-width="1.4" fill="none"/></svg></div>
  <div class="nav-arrow" style="left:1101px;top:245px"><svg width="12" height="12" viewBox="0 0 10 10"><path d="M1 5h8M5.5 1.5L9 5 5.5 8.5" stroke="#0b1424" stroke-width="1.4" fill="none"/></svg></div>
  <div class="btn btn-green" style="left:514px;top:428px;width:171px;height:39px">EXPLORE PROGRAMS <span class="arrow"><svg width="12" height="12" viewBox="0 0 10 10"><path d="M1 5h8M5.5 1.5L9 5 5.5 8.5" stroke="#12883b" stroke-width="1.4" fill="none"/></svg></span></div>
</section>

<!-- TESTIMONIALS -->
<section>
  <h2 class="section-title" style="top:1822px">What Our Client Says</h2>
  <div class="nav-arrow" style="left:73px;top:1992px"><svg width="12" height="12" viewBox="0 0 10 10"><path d="M9 5H1M4.5 1.5L1 5l3.5 3.5" stroke="#0b1424" stroke-width="1.4" fill="none"/></svg></div>
  <div class="nav-arrow" style="left:1101px;top:1992px"><svg width="12" height="12" viewBox="0 0 10 10"><path d="M1 5h8M5.5 1.5L9 5 5.5 8.5" stroke="#0b1424" stroke-width="1.4" fill="none"/></svg></div>

  <div class="testi" style="left:121px">
    <div class="ph photo" role="img" aria-label="Client running across a gym floor" style="background:linear-gradient(180deg,#6a6e74,#3b3f46)"></div>
    <div class="avatar" role="img" aria-label="Client portrait"></div>
    <div class="name">Marlene K.</div>
    <div class="stars"><svg width="60" height="11" viewBox="0 0 60 11"><g fill="#f2b01e"><path id="s" d="M5.5 0l1.6 3.5 3.9.4-2.9 2.6.8 3.8-3.4-2-3.4 2 .8-3.8L0 3.9l3.9-.4z"/><use href="#s" x="12"/><use href="#s" x="24"/><use href="#s" x="36"/><use href="#s" x="48"/></g></svg></div>
    <svg class="qmark" width="48" height="36" viewBox="0 0 48 36"><path d="M0 0h20v20L10 36H4l6-16H0zM26 0h20v20L36 36h-6l6-16H26z" fill="#e2e2d6"/></svg>
    <p class="quote">"Lorem ipsum dolor sit amet, consectetur adipiscing elit. Morbi finibus tortor magna. Mauris quis diam sem. Suspendisse consequat porttitor aliquam."</p>
  </div>
  <div class="testi" style="left:609px">
    <div class="ph photo" role="img" aria-label="Athlete pressing a barbell overhead" style="background:linear-gradient(180deg,#50555d,#2b2f36)"></div>
    <div class="avatar" role="img" aria-label="Client portrait"></div>
    <div class="name">Marlene K.</div>
    <div class="stars"><svg width="60" height="11" viewBox="0 0 60 11"><g fill="#f2b01e"><path id="s2" d="M5.5 0l1.6 3.5 3.9.4-2.9 2.6.8 3.8-3.4-2-3.4 2 .8-3.8L0 3.9l3.9-.4z"/><use href="#s2" x="12"/><use href="#s2" x="24"/><use href="#s2" x="36"/><use href="#s2" x="48"/></g></svg></div>
    <svg class="qmark" width="48" height="36" viewBox="0 0 48 36"><path d="M0 0h20v20L10 36H4l6-16H0zM26 0h20v20L36 36h-6l6-16H26z" fill="#e2e2d6"/></svg>
    <p class="quote">"Lorem ipsum dolor sit amet, consectetur adipiscing elit. Morbi finibus tortor magna. Mauris quis diam sem. Suspendisse consequat porttitor aliquam."</p>
  </div>
</section>

<!-- BLOG -->
<section>
  <h2 class="abs display" style="left:119px;top:2176px;font-size:33px;font-weight:500">Latest Blog &amp; Resources</h2>
  <div class="btn btn-green" style="left:932px;top:2179px;width:145px;height:39px">VIEW ALL BLOG <span class="arrow"><svg width="12" height="12" viewBox="0 0 10 10"><path d="M1 5h8M5.5 1.5L9 5 5.5 8.5" stroke="#12883b" stroke-width="1.4" fill="none"/></svg></span></div>

  <div class="ph blog-img" role="img" aria-label="Two athletes bent over catching breath beside a barbell" style="left:121px;background:linear-gradient(180deg,#3e434a,#262a30)"></div>
  <div class="ph blog-img" role="img" aria-label="Athlete skipping rope in a competition arena" style="left:446px;background:linear-gradient(180deg,#10161f,#353b44)"></div>
  <div class="ph blog-img" role="img" aria-label="Athlete in mint outfit running on the gym floor" style="left:771px;background:linear-gradient(180deg,#6b6f75,#3d4148)"></div>

  <div class="blog-title" style="left:127px">How to Fix the Dreaded<br>Elbow Rebend in Your Jerk</div>
  <div class="blog-go" style="left:393px"><svg width="11" height="11" viewBox="0 0 10 10"><path d="M1 5h8M5.5 1.5L9 5 5.5 8.5" stroke="#fff" stroke-width="1.3" fill="none"/></svg></div>
  <div class="blog-rule" style="left:121px"></div>
  <div class="blog-title" style="left:452px">Tips To Avoid Injury<br>During Workouts</div>
  <div class="blog-go" style="left:718px"><svg width="11" height="11" viewBox="0 0 10 10"><path d="M1 5h8M5.5 1.5L9 5 5.5 8.5" stroke="#fff" stroke-width="1.3" fill="none"/></svg></div>
  <div class="blog-rule" style="left:446px"></div>
  <div class="blog-title" style="left:777px">Maximize Your Potential as a<br>CoreFit Masters Athlete</div>
  <div class="blog-go" style="left:1043px"><svg width="11" height="11" viewBox="0 0 10 10"><path d="M1 5h8M5.5 1.5L9 5 5.5 8.5" stroke="#fff" stroke-width="1.3" fill="none"/></svg></div>
  <div class="blog-rule" style="left:771px"></div>
</section>

<!-- LOCATIONS -->
<section>
  <div class="loc-card">
    <h2>Our Locations</h2>
    <div class="loc-row active" style="top:73px"><span class="pin"><svg width="10" height="13" viewBox="0 0 10 13"><path d="M5 12S1 7.5 1 5a4 4 0 018 0c0 2.5-4 7-4 7z" fill="none" stroke="currentColor" stroke-width="1.4"/><circle cx="5" cy="5" r="1.4" fill="currentColor"/></svg></span>San Diego (HQ)</div>
    <div class="loc-row" style="top:118px"><span class="pin"><svg width="10" height="13" viewBox="0 0 10 13"><path d="M5 12S1 7.5 1 5a4 4 0 018 0c0 2.5-4 7-4 7z" fill="none" stroke="currentColor" stroke-width="1.4"/><circle cx="5" cy="5" r="1.4" fill="currentColor"/></svg></span>Boston</div>
    <div class="loc-row" style="top:163px"><span class="pin"><svg width="10" height="13" viewBox="0 0 10 13"><path d="M5 12S1 7.5 1 5a4 4 0 018 0c0 2.5-4 7-4 7z" fill="none" stroke="currentColor" stroke-width="1.4"/><circle cx="5" cy="5" r="1.4" fill="currentColor"/></svg></span>Miami</div>
    <div class="loc-row" style="top:208px"><span class="pin"><svg width="10" height="13" viewBox="0 0 10 13"><path d="M5 12S1 7.5 1 5a4 4 0 018 0c0 2.5-4 7-4 7z" fill="none" stroke="currentColor" stroke-width="1.4"/><circle cx="5" cy="5" r="1.4" fill="currentColor"/></svg></span>Seattle</div>
    <div class="loc-row" style="top:253px"><span class="pin"><svg width="10" height="13" viewBox="0 0 10 13"><path d="M5 12S1 7.5 1 5a4 4 0 018 0c0 2.5-4 7-4 7z" fill="none" stroke="currentColor" stroke-width="1.4"/><circle cx="5" cy="5" r="1.4" fill="currentColor"/></svg></span>DC</div>
  </div>
  <div class="ph" role="img" aria-label="San Diego waterfront skyline seen from a pier" style="left:532px;top:2720px;width:546px;height:311px;border:4px solid var(--blue-line);border-radius:6px;background:linear-gradient(180deg,#3b78c6 0%,#8db6e3 45%,#5f7488 65%,#1d2a36 100%)"></div>
  <div class="abs" style="left:679px;top:3000px;width:254px;height:27px;background:var(--navy-2);border-radius:14px 14px 0 0;font-size:11.5px;font-weight:700;display:flex;align-items:center;justify-content:center">2210 Harbor Lane, San Diego California 92101</div>
</section>

<!-- NEWSLETTER -->
<section>
  <div class="bigword">CORVANE ATHLETICS</div>
  <div class="news">
    <h2>Stay Connected with Corvane</h2>
    <p>Get exclusive workouts, nutrition advice, and updates.</p>
    <div class="field">Enter Your Email
      <div class="sub">SUBSCRIBE <span class="arrow" style="width:26px;height:26px;border-radius:50%;border:1.5px solid #fff;display:flex;align-items:center;justify-content:center"><svg width="11" height="11" viewBox="0 0 10 10"><path d="M1 5h8M5.5 1.5L9 5 5.5 8.5" stroke="#fff" stroke-width="1.4" fill="none"/></svg></span></div>
    </div>
  </div>
  <div class="ph" role="img" aria-label="Female athlete holding a loaded barbell overhead in a split stance" style="left:210px;top:3068px;width:262px;height:496px;background:linear-gradient(180deg,rgba(58,66,80,.95),rgba(38,46,62,.95) 55%,rgba(30,36,52,.9));border-radius:120px 120px 8px 8px"></div>
</section>

<!-- FOOTER -->
<footer class="footer">
  <div class="fcol" style="left:120px;top:52px;width:205px">
    <div class="logo-text" style="font-size:18px;margin-bottom:14px">CORVANE ATHLETICS</div>
    <p style="font-size:8.8px;line-height:15px;color:#d3d8e0">At Corvane Athletics, we believe that everyone has the power to be stronger, faster, and more resilient. Our mission is simple: to provide world-class training, expert guidance, and a supportive community that inspires you to push past limits — whether in one of our 5 state-of-the-art gyms across the U.S.</p>
  </div>
  <div class="fdiv" style="left:338px"></div>
  <div class="fcol" style="left:360px">
    <h4>Contact Us</h4>
    <div class="fcontact"><span class="c"><svg width="10" height="10" viewBox="0 0 10 10"><path d="M2 1l2 2-1 1.5a6 6 0 002.5 2.5L7 6l2 2-1.5 1.5C4 9.5.5 6 .5 2.5z" fill="#fff"/></svg></span>800-555-0142</div>
    <div class="fcontact"><span class="c"><svg width="10" height="8" viewBox="0 0 10 8"><rect x=".5" y=".5" width="9" height="7" fill="none" stroke="#fff"/><path d="M.5.5L5 4.5 9.5.5" fill="none" stroke="#fff"/></svg></span><span style="color:var(--green-bright)">hello@corvaneathletics.example</span></div>
  </div>
  <div class="fdiv" style="left:518px"></div>
  <div class="fcol" style="left:558px"><h4>Main Link</h4><ul><li>Home</li><li>About</li><li>Programs</li><li>Blog</li><li>Location</li><li>Contact Us</li></ul></div>
  <div class="fcol" style="left:698px"><h4>Our Location</h4><ul><li>San Diego (HQ)</li><li>Boston</li><li>Miami</li><li>Seattle</li><li>DC</li></ul></div>
  <div class="fcol" style="left:870px;top:58px"><h4>Shop</h4><ul><li>Merch</li><li>Apparel</li><li>Equipment</li><li>Supplements</li><li>PDFs</li><li>Programs</li></ul></div>
  <div class="fcol" style="left:998px">
    <h4>Follow Us</h4>
    <div class="social"><span class="c"></span>Friendloop</div>
    <div class="social"><span class="c"></span>Chirpline</div>
    <div class="social"><span class="c"></span>Snapframe</div>
    <div class="social"><span class="c"></span>Vidstream</div>
  </div>
  <div class="abs" style="left:120px;top:236px;width:957px;height:1px;background:#1d283a"></div>
  <div class="abs" style="left:120px;top:244px;font-size:8.5px;color:#d3d8e0">© 2025 Corvane Athletics All Rights Reserved.</div>
  <div class="abs" style="left:895px;top:242px;font-size:8.5px;color:#d3d8e0;word-spacing:3px">Privacy &nbsp;|&nbsp; CookiesTerms &nbsp;|&nbsp; Conditions</div>
</footer>

</div>
</body>
</html>
```